Data/Computer Security company needs a brochure design

We need a brochure design for Vantage Ledger.
We deliver security solutions that manage critical risks, protect vital information and provide regulatory compliance. (mostly professional offices and small businesses with an emphasis in financial services) Optimal security is achieved through agent-based auditing and network activity monitoring.
Specialists in the area of helping Broker/Dealers and Independent Financial Service Representatives measure field office security, threat readiness and compliance with current policies and procedures. We provide auditors with clear, concise reports of policy deviations along with guidance in closing gaps, weaknesses or deficiencies.
Our services allow audit staff efficiency and productivity in their process while ensuring the field offices are utilizing best security practices and exercising the appropriate level of diligence and care in protecting the client information entrusted to them.
More about process and services can be seen on our website - www.vantageledger.example
We use blues and grays in our designs.

```html
<!DOCTYPE html>
<html lang="en">
<head>
<meta charset="utf-8">
<title>Vantage Ledger — Security Brochure</title>
<link href="https://fonts.googleapis.com/css2?family=Lato:wght@300;400;700;900&display=swap" rel="stylesheet">
<style>
  :root{
    --brand-blue:#2a3b9e;
    --ink:#3b3b3b;
    --soft-ink:#555;
    --panel-gray:#ececec;
    --night:#1d1d1d;
    --paper:#ffffff;
    --page-bg:#ffffff;
    --cover-text:#f0f0f0;
  }
  *{margin:0;padding:0;box-sizing:border-box;}
  html,body{width:1200px;height:560px;overflow:hidden;background:var(--page-bg);}
  body{position:relative;font-family:"Lato",Arial,sans-serif;color:var(--ink);font-weight:300;}

  .spread{position:absolute;background:var(--paper);box-shadow:0 3px 6px rgba(0,0,0,.28);overflow:hidden;}
  .spread svg.shapes{position:absolute;left:0;top:0;}
  .abs{position:absolute;}

  /* Outside spread */
  .outside{left:22px;top:24px;width:1120px;height:242px;}
  .pricing-title{left:150px;top:52px;font-size:9.6px;color:var(--brand-blue);font-weight:400;letter-spacing:.3px;}
  .pricing-fee{left:150px;top:66px;font-size:10.2px;color:#222;font-weight:400;white-space:nowrap;}
  .pricing-fee b{font-weight:900;}
  .pricing-note{left:150px;top:79px;font-size:6.2px;color:var(--soft-ink);white-space:nowrap;}
  .pricing-copy{left:150px;top:99px;width:162px;font-size:8.4px;line-height:11.2px;color:var(--ink);}
  .brand-name{left:392px;top:146px;font-size:13px;font-weight:900;color:var(--brand-blue);letter-spacing:.2px;white-space:nowrap;}
  .address{left:395px;top:181px;font-size:6.2px;line-height:8.6px;color:var(--soft-ink);font-style:normal;white-space:nowrap;}
  .address .web{color:var(--brand-blue);font-size:6.6px;margin-top:2px;display:block;}
  .cover-photos{left:865px;top:76px;width:136px;height:20px;display:flex;gap:2px;}
  .cover-photos div{flex:1;background:linear-gradient(135deg,#5f6878,#c9ced6 60%,#4d5666);}
  .cover-rule{left:865px;width:136px;height:1px;background:#9a9a9a;}
  .cover-title{left:865px;top:104px;width:136px;font-size:7.2px;line-height:9.4px;color:var(--cover-text);font-weight:300;}
  .cover-title span{display:block;white-space:nowrap;}
  .cover-title b{font-weight:900;}

  /* Inside spread */
  .inside{left:56px;top:294px;width:1120px;height:240px;}
  .lead{left:20px;top:28px;width:322px;font-size:7.6px;line-height:9.6px;font-weight:900;color:var(--brand-blue);}
  .column{position:absolute;font-size:5.3px;line-height:7px;color:var(--soft-ink);}
  .column h3{font-size:6.8px;line-height:8px;font-weight:400;color:var(--brand-blue);letter-spacing:.1px;margin-bottom:2px;}
  .column h3.gap{margin-top:5px;}
  .column ul{list-style:none;}
  .column li{position:relative;padding-left:6px;margin-bottom:1.5px;}
  .column li::before{content:"•";position:absolute;left:0;}
  .column ul.indent li{padding-left:10px;}
  .column ul.indent li::before{left:4px;}
  .column ol{list-style:none;}
  .column ol li{padding-left:7px;margin:3px 0;}
  .column ol li::before{content:attr(data-n);font-weight:700;color:#333;}
  .column strong{font-weight:700;color:#333;}
  .column p{margin-bottom:3px;}
  .column p.hang{padding-left:7px;}
  .col-problem{left:20px;top:52px;width:152px;}
  .col-method{left:194px;top:52px;width:146px;}
  .col-help{left:394px;top:50px;width:146px;}
  .col-realtime{left:566px;top:52px;width:150px;}
  .col-filter{left:744px;top:60px;width:176px;}
  .threat-art{left:926px;top:0;width:194px;height:240px;}
</style>
</head>
<body>

<!-- Outside spread -->
<section class="spread outside">
  <svg class="shapes" width="1120" height="242" viewBox="0 0 1120 242" aria-hidden="true">
    <path d="M0 0 H110 C86 80 84 170 96 242 H0 Z" fill="var(--panel-gray)"/>
    <path d="M106 0 C80 80 78 170 90 242 L102 242 C92 170 94 80 118 0 Z" fill="var(--brand-blue)"/>
    <path d="M690 0 C714 80 714 170 692 242 H1120 V0 Z" fill="var(--night)"/>
    <path d="M676 0 C702 80 702 170 680 242 L694 242 C716 170 716 80 690 0 Z" fill="var(--brand-blue)"/>
  </svg>

  <h2 class="abs pricing-title">PRICING</h2>
  <p class="abs pricing-fee">Monthly fee of <b>$13.50</b> per computer.</p>
  <p class="abs pricing-note">Sales tax may be applicable in some areas.</p>
  <p class="abs pricing-copy">With Vantage Ledger's unique services, the security of personal and confidential information does not need to be burdensome, intrusive or expensive.</p>

  <div class="abs brand-name">Vantage Ledger</div>
  <address class="abs address">
    4820 Harbor Point Dr<br>Suite B12<br>Lakemont, IA 50999<br>(555) 014 2290
    <span class="web">www.vantageledger.example</span>
  </address>

  <div class="abs cover-rule" style="top:73px"></div>
  <div class="abs cover-photos">
    <div role="img" aria-label="Photo of hands typing on a laptop keyboard"></div>
    <div role="img" aria-label="Photo of an office workstation"></div>
    <div role="img" aria-label="Photo of a hand holding a security key"></div>
  </div>
  <div class="abs cover-rule" style="top:99px"></div>
  <h1 class="abs cover-title">
    <span style="letter-spacing:.85px">PROTECTING YOUR CLIENTS,</span>
    <span style="letter-spacing:.75px">PROTECTING YOUR BUSINESS</span>
    <span style="letter-spacing:.2px">COMPUTER SECURITY SOLUTIONS</span>
    <span style="letter-spacing:.9px">FROM <b>VANTAGE LEDGER</b></span>
  </h1>
  <div class="abs cover-rule" style="top:143px"></div>
</section>

<!-- Inside spread -->
<section class="spread inside">
  <svg class="shapes" width="1120" height="240" viewBox="0 0 1120 240" aria-hidden="true">
    <rect x="0" y="0" width="380" height="240" fill="var(--panel-gray)"/>
  </svg>

  <p class="abs lead">Cybercrime and privacy concerns are an ever-growing business threat and Vantage Ledger has a series of affordable, actionable steps to help protect both you and your clients.</p>

  <div class="column col-problem">
    <h3>HOW BIG IS THE PROBLEM?</h3>
    <ul>
      <li>Anti-virus vendors report receiving 60,000 new malware samples every day</li>
      <li>Approximately 1500 new malware sites are created per day</li>
      <li>Sixty-percent of top Searchly search terms return malicious sites within the first 100 results</li>
    </ul>
    <h3 class="gap">WHY DO THEY DO IT?</h3>
    <ul>
      <li>Northern Pharmacy spam campaign can net $16,000 per day</li>
      <li>Affiliate webmaster redirecting to a scareware site can net $180,000 a year</li>
      <li>Credit card information sells for $15 to $200 (at the higher end if it includes the PIN)</li>
      <li>Botnet rental runs as little as $10-$65 per hour</li>
      <li>One million e-mail addresses can be purchased for $20-$100</li>
      <li>Complete set of data on a US resident is only $5 to $8</li>
      <li>A continuous 24-hour Botnet for DDoS attacks can be launched for as little as $50</li>
      <li>Stolen bank account details go for $1 to $1,500 depending on level of detail and balance</li>
    </ul>
  </div>

  <div class="column col-method">
    <h3>HOW DO THEY DO IT?</h3>
    <p>They do it by exploiting weaknesses in common software like WebNavigator, OfficeSuite Pro, DocView Reader, MotionPlay and RunTime. Software developers have created 'crimeware' applications designed to exploit known weaknesses in software on the target computers. The malware is delivered in numerous ways:</p>
    <ul class="indent">
      <li>A pop-up in your web browser saying you have a virus</li>
      <li>In a pdf or poisoned OfficeSuite Pro email attachment</li>
      <li>A link in a Circlenet message</li>
      <li>A link in your Searchly search results</li>
      <li>A contaminated USB drive</li>
      <li>Inside a free game or download</li>
      <li>Poisoned ads on prominent websites</li>
      <li>Through security weaknesses in old, un-patched software</li>
    </ul>
  </div>

  <div class="column col-help">
    <h3>HOW WE HELP YOU PROTECT YOURSELF</h3>
    <p>Vantage Ledger's five-point program helps you understand and manage your risks. Protecting your business need not be burdensome, time consuming or expensive.</p>
    <ol>
      <li data-n="1."><strong>Patch Management</strong> – Utilizing the same tools used by the Military, we monitor the applications installed on each computer daily. We compare this list to known vulnerabilities and updates. If any of your applications are at risk, we notify you and provide instructions on how to update the appropriate application.</li>
      <li data-n="2."><strong>New Application Monitoring</strong> – All newly installed applications are screened for suitability and consistency. You are notified of any new applications installed which seem to be out of the ordinary. In many cases, we are able to identify malware soon after it has been installed. We also help catch non-approved user installed applications.</li>
      <li data-n="3."><strong>Anti-Virus Monitoring</strong> – Daily, each computer is checked for functioning and up-to-date Anti-virus software.</li>
    </ol>
  </div>

  <div class="column col-realtime">
    <ol>
      <li data-n="4." style="margin-top:0"><strong>Realtime Internet Navigation and Security Services</strong> – Comprehensive security for your network through award-winning phishing, botnet and malware site protection. Our Web filtering service delivers network security services through the DNS layer blocking known malicious or infected sites from resolving on your network. Since infected sites are prevented from resolving, phishing attempts and malicious content are blocked from reaching your network thereby providing the most efficient protection available.</li>
    </ol>
    <p class="hang">If one of your computers did become infected, built-in botnet protection stops trojans, key loggers, and other persistent malware and viruses on machines in your network from sending out confidential data and personal information to hackers outside the firewall. We will alert you if we detect certain botnets on your network to enable you to take immediate action.</p>
    <p class="hang">Malware site protection stops users from unknowingly going to known sites that can infect user machines, typically through the use of drive-by downloads and browser vulnerabilities.</p>
  </div>

  <div class="column col-filter">
    <p>This prevents infected content from reaching your network where it can cause harm and spread to other machines. Our list of hundreds of thousands of known bad Web addresses is updated every five minutes to provide you with the most up-to-date protection.</p>
    <p>Web content filtering is also provided, allowing access to a rich database of more than 50 categories and millions of domains. This allows you to control which sites can be accessed on your network. The ability to set content filtering policies on a per-site or per-network basis, giving you greater control when applying access policies to Internet usage.</p>
    <ol>
      <li data-n="5."><strong>Security Awareness Program</strong> – Your staff can be one of your greatest strengths or an easily exploitable weakness. Cybercriminals prey on the untrained to gain access. We provide a program to help educate your staff on techniques currently in use by cybercriminals and how to best deal with these threats. This program is delivered through short, weekly emailed security briefings; each taking no more than two minutes to read.</li>
    </ol>
  </div>

  <svg class="abs threat-art" width="194" height="240" viewBox="0 0 194 240" role="img" aria-label="Illustration of dark blue code text with threat words such as malware, virus, spam and phishing">
    <defs>
      <linearGradient id="threatTone" x1="0" y1="0" x2="1" y2="1">
        <stop offset="0" stop-color="#2c3e78"/>
        <stop offset=".55" stop-color="#16224a"/>
        <stop offset="1" stop-color="#0b1230"/>
      </linearGradient>
    </defs>
    <path d="M28 0 C2 80 4 170 34 240 H194 V0 Z" fill="url(#threatTone)"/>
    <path d="M18 0 C-8 80 -6 170 22 240 L34 240 C4 170 2 80 28 0 Z" fill="var(--brand-blue)"/>
  </svg>
</section>

</body>
</html>
```